RWT Fittings Ltd Business Cards

We need a business card with our business logo. We provide window and door installations on high-rises in west coast British Colombia, Canada.

I would like my business information and details on one side of the card, and the other side the company name with logo

Target Market(s)

General Contractors

Industry/Entity Type

Construction

Contact Information for Business Card

one side i want my company name and logo in the dark theme logo that i provided

Requirements
Must have
• Marco Peltieri, 16045518293, RWTFittings@mailbox-demo.com, 1407-5194 Linden Row Burnaby BC, V5H 2K9, Owner & Manager

```html
<!DOCTYPE html>
<html lang="en">
<head>
<meta charset="UTF-8">
<title>RWT Fittings Ltd – Business Cards</title>
<link rel="stylesheet" href="https://fonts.googleapis.com/css2?family=Montserrat:wght@400;500;700&display=swap">
<style>
  :root {
    --backdrop: #b3b3b3;
    --card: #2b2b2b;
    --accent: #29a8e0;
    --ink-light: #e6e6e6;
    --ink-muted: #cfcfcf;
    --mark-dark: #4a4a4a;
  }
  * { box-sizing: border-box; margin: 0; padding: 0; }
  html, body {
    width: 1200px;
    height: 900px;
    overflow: hidden;
    background: var(--backdrop);
    font-family: "Montserrat", sans-serif;
  }
  .sheet {
    width: 1200px;
    height: 900px;
    display: flex;
    flex-direction: column;
    align-items: center;
    justify-content: center;
    gap: 40px;
  }
  .card {
    width: 700px;
    height: 400px;
    background: var(--card);
    border-bottom: 4px solid var(--accent);
    position: relative;
    box-shadow: 0 10px 24px rgba(0,0,0,0.3);
  }

  /* Front side */
  .card-front {
    display: flex;
    align-items: center;
  }
  .brand {
    width: 360px;
    display: flex;
    align-items: center;
    justify-content: center;
    gap: 12px;
  }
  .brand-square {
    width: 30px;
    height: 30px;
    background: var(--accent);
  }
  .brand-name {
    color: var(--accent);
    font-weight: 700;
    font-size: 26px;
    letter-spacing: 0.5px;
    white-space: nowrap;
  }
  .details {
    border-left: 2px solid var(--accent);
    padding: 18px 0 18px 26px;
    height: 230px;
    display: flex;
    flex-direction: column;
    justify-content: space-between;
  }
  .person-name {
    color: var(--accent);
    font-weight: 700;
    font-size: 26px;
    line-height: 1.1;
  }
  .person-role {
    color: var(--ink-light);
    font-size: 14px;
    margin-top: 4px;
  }
  .address {
    color: var(--ink-light);
    font-size: 15px;
    line-height: 1.35;
  }
  .contact-list {
    list-style: none;
    display: flex;
    flex-direction: column;
    gap: 8px;
  }
  .contact-item {
    display: flex;
    align-items: center;
    gap: 10px;
    color: var(--ink-light);
    font-size: 15px;
  }
  .contact-icon {
    width: 18px;
    height: 18px;
    fill: var(--accent);
    flex: none;
  }

  /* Back side */
  .card-back {
    display: flex;
    align-items: center;
    justify-content: center;
    gap: 18px;
  }
  .back-square {
    width: 56px;
    height: 56px;
    background: var(--mark-dark);
  }
  .back-name {
    color: var(--mark-dark);
    font-weight: 700;
    font-size: 50px;
    letter-spacing: 1px;
    white-space: nowrap;
  }
</style>
</head>
<body>
  <main class="sheet">
    <section class="card card-front" aria-label="Business card front">
      <div class="brand">
        <span class="brand-square"></span>
        <span class="brand-name">RWT Fittings Ltd</span>
      </div>
      <div class="details">
        <div class="person">
          <h1 class="person-name">Marco Peltieri</h1>
          <p class="person-role">Owner &amp; Manager</p>
        </div>
        <p class="address">1407-5194 Linden Row<br>Burnaby BC, V5H 2K9</p>
        <ul class="contact-list">
          <li class="contact-item">
            <svg class="contact-icon" viewBox="0 0 24 24" aria-hidden="true">
              <path d="M6.6 10.8a15.1 15.1 0 0 0 6.6 6.6l2.2-2.2c.3-.3.7-.4 1-.2 1.1.4 2.3.6 3.6.6.6 0 1 .4 1 1V20c0 .6-.4 1-1 1A17 17 0 0 1 3 4c0-.6.4-1 1-1h3.5c.6 0 1 .4 1 1 0 1.3.2 2.5.6 3.6.1.3 0 .7-.2 1z"/>
            </svg>
            <span>16045518293</span>
          </li>
          <li class="contact-item">
            <svg class="contact-icon" viewBox="0 0 24 24" aria-hidden="true">
              <path d="M3 5h18v14H3z M3 5l9 7 9-7" fill="none" stroke="#29a8e0" stroke-width="0"/>
              <path d="M2 5v14h20V5H2zm10 7.5L4.5 7h15L12 12.5z"/>
            </svg>
            <span>RWTFittings@mailbox-demo.com</span>
          </li>
        </ul>
      </div>
    </section>

    <section class="card card-back" aria-label="Business card back">
      <span class="back-square"></span>
      <span class="back-name">RWT Fittings Ltd</span>
    </section>
  </main>
</body>
</html>
```